Tollin Waste Website Design

Our new start-up needs a website design. We plan to help businesses find more sustainable ways to manage their waste. Our initial website aims to gather contact data from potential business customers and comprehensive information from waste facilities and waste transporters. We have a logo design (attached) which we would like included in the website design. I have also attached a number of pages that describe what information should appear on each page as well as a web design brief file that describes the look we are after.

```html
<!DOCTYPE html>
<html lang="en">
<head>
<meta charset="utf-8">
<title>Tollin Waste — Home</title>
<link href="https://fonts.googleapis.com/css2?family=Montserrat:wght@500;700&family=Open+Sans:wght@400;600;700&display=swap" rel="stylesheet">
<style>
:root{
  --page-bg:#f6f8ec;
  --lime:#8cc63f;
  --leaf:#5a9628;
  --white:#ffffff;
  --footer:rgba(20,24,16,.72);
  --photo-a:#3e4a34;
  --photo-b:#4f6b35;
  --photo-c:#2b3324;
}
*{margin:0;padding:0;box-sizing:border-box}
html,body{width:1010px;height:1200px;overflow:hidden}
body{background:var(--page-bg);position:relative;font-family:"Open Sans",sans-serif;color:var(--white)}
.screen{position:absolute;left:89px;width:832px;height:492px;overflow:hidden;box-shadow:0 6px 24px rgba(0,0,0,.25)}
.screen--home{top:80px}
.screen--signup{top:627px}
.hero-photo{position:absolute;inset:0;background:
  radial-gradient(ellipse at 62% 45%,var(--photo-b) 0%,transparent 60%),
  linear-gradient(135deg,var(--photo-a) 0%,#465a36 50%,var(--photo-c) 100%)}
.brand{position:absolute;left:78px;top:34px;display:flex;align-items:center;gap:10px}
.brand-mark{width:44px;height:44px;border:3px solid var(--lime);border-radius:50%}
.brand-name{font-family:"Montserrat",sans-serif;font-weight:700;font-size:26px;color:var(--white);letter-spacing:.5px}
.nav{position:absolute;top:49px;left:346px;right:70px;font-family:"Montserrat",sans-serif;font-weight:500;font-size:12px}
.nav span{position:absolute;white-space:nowrap}
.nav svg{position:absolute}
.hero-title{position:absolute;top:150px;width:100%;text-align:center;font-family:"Montserrat",sans-serif;font-weight:700;font-size:38px;letter-spacing:.5px}
.hero-sub{position:absolute;top:207px;width:100%;text-align:center;font-size:22px}
.audience{position:absolute;top:259px;width:130px;margin-left:-65px;text-align:center}
.audience-ring{width:100px;height:100px;margin:0 auto;border:1.5px solid var(--white);border-radius:50%;background:rgba(20,24,16,.35);display:flex;align-items:center;justify-content:center}
.audience-label{margin-top:17px;font-weight:700;font-size:13px;white-space:nowrap}
.site-footer{position:absolute;left:0;right:0;bottom:0;height:55px;background:var(--footer);text-align:center;font-size:10px;line-height:55px}
.dim{position:absolute;inset:0;background:rgba(10,12,8,.55)}
.signup{position:absolute;left:203px;top:32px;width:426px;height:426px;border-radius:50%;background:var(--leaf);border:5px solid var(--white);text-align:center}
.signup-mark{width:76px;height:76px;margin:40px auto 0;border:6px solid var(--white);border-radius:50%}
.signup-text{margin:12px auto 0;width:360px;font-weight:600;font-size:16px;line-height:25.6px}
.signup-input{display:block;margin:19px auto 0;width:316px;height:41px;background:var(--white);color:#333;font-size:11px;text-align:left;padding-left:17px;line-height:41px}
.signup-submit{display:block;margin:19px auto 0;width:110px;height:44px;border-radius:22px;background:var(--lime);font-weight:700;font-size:14px;letter-spacing:.5px;line-height:44px}
.signup-close{margin-top:13px;font-weight:700;font-size:18px}
</style>
</head>
<body>

<section class="screen screen--home">
  <div class="hero-photo" role="img" aria-label="Photo of a recycling conveyor belt carrying sorted waste"></div>
  <div class="brand"><div class="brand-mark"></div><div class="brand-name">Tollin Waste</div></div>
  <nav class="nav">
    <span style="left:0">ABOUT US</span>
    <span style="left:88px">WHAT WE DO</span>
    <span style="left:196px">RESOURCES</span>
    <span style="left:295px">CONTACT US</span>
    <svg style="left:400px;top:2px" width="11" height="11" viewBox="0 0 11 11"><circle cx="4.5" cy="4.5" r="3.3" fill="none" stroke="#fff" stroke-width="1.8"/><line x1="7" y1="7" x2="10" y2="10" stroke="#fff" stroke-width="2"/></svg>
  </nav>
  <h1 class="hero-title">WELCOME TO TOLLIN WASTE</h1>
  <p class="hero-sub">Take control of your waste here</p>

  <div class="audience" style="left:262px">
    <div class="audience-ring">
      <svg width="54" height="50" viewBox="0 0 54 50" fill="#8cc63f"><polygon points="27,2 38,20 30,20 27,15 19,28 12,24"/><polygon points="44,26 52,40 34,40 34,46 26,37 34,28 34,34 45,34 38,22"/><polygon points="2,40 10,26 17,30 12,34 18,34 18,46 8,46"/></svg>
    </div>
    <div class="audience-label">WASTE PRODUCERS</div>
  </div>
  <div class="audience" style="left:410px">
    <div class="audience-ring">
      <svg width="40" height="58" viewBox="0 0 40 58"><path d="M14 14 C10 8 18 6 14 1 M26 14 C30 8 22 6 28 1" stroke="#8cc63f" stroke-width="2" fill="none"/><polygon points="10,18 30,18 32,52 8,52" fill="#8cc63f"/><rect x="5" y="52" width="30" height="4" fill="#8cc63f"/><circle cx="20" cy="34" r="5" fill="#2b3324"/></svg>
    </div>
    <div class="audience-label">WASTE FACILITIES</div>
  </div>
  <div class="audience" style="left:559px">
    <div class="audience-ring">
      <svg width="58" height="40" viewBox="0 0 58 40" fill="#8cc63f"><rect x="2" y="2" width="34" height="26" rx="2"/><path d="M38 10 H48 L56 20 V30 H38 Z"/><circle cx="14" cy="32" r="6" stroke="#2b3324" stroke-width="2"/><circle cx="46" cy="32" r="6" stroke="#2b3324" stroke-width="2"/></svg>
    </div>
    <div class="audience-label">WASTE TRANSPORTERS</div>
  </div>

  <footer class="site-footer">© Tollin Waste. All rights reserved.</footer>
</section>

<section class="screen screen--signup">
  <div class="hero-photo" role="img" aria-label="Photo of a recycling conveyor belt carrying sorted waste"></div>
  <div class="brand"><div class="brand-mark"></div><div class="brand-name">Tollin Waste</div></div>
  <nav class="nav">
    <span style="left:0">ABOUT US</span>
    <span style="left:88px">WHAT WE DO</span>
    <span style="left:196px">RESOURCES</span>
    <span style="left:295px">CONTACT US</span>
  </nav>
  <h1 class="hero-title">WELCOME TO TOLLIN WASTE</h1>
  <div class="audience" style="left:262px"><div class="audience-ring"></div><div class="audience-label">WASTE PRODUCERS</div></div>
  <div class="audience" style="left:410px"><div class="audience-ring"></div><div class="audience-label">WASTE FACILITIES</div></div>
  <div class="audience" style="left:559px"><div class="audience-ring"></div><div class="audience-label">WASTE TRANSPORTERS</div></div>
  <footer class="site-footer">© Tollin Waste. All rights reserved.</footer>
  <div class="dim"></div>

  <div class="signup">
    <div class="signup-mark"></div>
    <p class="signup-text">Welcome to TOLLIN Waste. We are just getting started. Please register your email address to receive updates from us.</p>
    <span class="signup-input">Email address</span>
    <span class="signup-submit">SUBMIT</span>
    <div class="signup-close">X</div>
  </div>
</section>

</body>
</html>
```